Ledgerwise Forge - WordPress Theme & Logo

Design a logo and Wordpress website design for Ledgerwise Forge. Ledgerwise Forge provides cryptocurrency development services to clients who need a team to create & continue developing a new cryptocurrency or who want to replace their current cryptocurrency development team. more details in the attached document.
Updates

Target Market(s)

Entrepreneurs who are building a business / platform that makes use of an underlying cryptocurrency.

Logo Text

LF or Ledgerwise Forge

Coding

Coded - Design and coding required

Font styles to use
Sans Serif

Requirements
Must have
• Professional logo, complete coded Wordpress theme for all pages, containing all specified links and buttons
Nice to have
• It would be nice if the buttons that are meant to integrate with Dealtrail contain the necessary code for that. I can provide any necessary Dealtrail details from my account.
Should not have
• Slow loading time

```html
<!DOCTYPE html>
<html lang="en">
<head>
<meta charset="utf-8">
<title>Ledgerwise Forge</title>
<link rel="stylesheet" href="https://fonts.googleapis.com/css2?family=Cabin:wght@400;500;600;700&family=Lato:ital,wght@0,400;0,700;1,400&display=swap">
<style>
:root{
  --green:#1fc46f;
  --green-dark:#12a85a;
  --navy:#0b111c;
  --navy-2:#141d2b;
  --ink:#222;
  --muted:#444;
  --gray-band:#f2f2f2;
  --white:#fff;
  --star:#f5a623;
}
*{box-sizing:border-box;margin:0;padding:0}
html,body{width:1200px;height:4058px;overflow:hidden}
body{font-family:"Lato",sans-serif;color:var(--ink);background:var(--white)}
h1,h2,h3,h4,.btn,.nav a,.brand{font-family:"Cabin",sans-serif}
section,header,footer{position:relative;width:1200px}
.btn{display:inline-block;border-radius:24px;font-weight:600;text-decoration:none;text-align:center}
.btn-green{background:var(--green);color:var(--white)}
.btn-white{background:var(--white);color:var(--green)}
.section-title{text-align:center;font-weight:400;font-size:33px;color:var(--ink)}
.section-title b{font-weight:700}
.rule{width:46px;height:4px;background:var(--green);margin:14px auto 0;border-radius:2px}

/* hero */
.hero{height:598px;background:var(--navy)}
.hero-art{position:absolute;inset:0 0 40px 0;background:radial-gradient(ellipse at 55% 25%,#2a3b4e 0%,#121b28 45%,var(--navy) 80%)}
.topbar{position:absolute;top:26px;left:55px;right:55px;height:46px;display:flex;align-items:center}
.brand{display:flex;align-items:center;gap:10px;color:var(--white);font-weight:700;font-size:17px;letter-spacing:.2px}
.brand-dot{width:22px;height:22px;border-radius:50%;background:var(--green)}
.nav{margin-left:92px;display:flex;gap:34px}
.nav a{color:var(--white);font-size:11px;font-weight:700;text-decoration:none}
.topbar .btn{margin-left:auto;width:146px;height:44px;line-height:44px;font-size:15px}
.hero h1{position:absolute;top:222px;width:100%;text-align:center;color:var(--white);font-size:34px;font-weight:700;line-height:52px}
.hero .cta{position:absolute;top:348px;left:462px;width:276px;height:45px;line-height:45px;font-size:15px}
.scroll-down{position:absolute;top:488px;left:580px}
.hero-wave{position:absolute;bottom:0;left:0}

/* intro */
.intro{height:272px;background:var(--gray-band);margin-top:0}
.intro p{position:absolute;top:80px;left:170px;width:860px;text-align:center;font-size:20px;line-height:38px;color:#333}

/* why */
.why{height:603px;background:var(--white)}
.why .section-title{padding-top:80px}
.cards{position:absolute;top:158px;left:151px;display:flex;gap:29px}
.card{width:280px;height:360px;background:var(--white);box-shadow:0 6px 14px rgba(0,0,0,.18);text-align:center;padding:6px}
.card-img{height:183px;border-radius:3px}
.card h3{margin-top:20px;font-size:20px;font-weight:700}
.card p{margin:8px 16px 0;font-size:15px;line-height:29px;color:var(--muted)}
.more{display:inline-block;margin-top:8px;font-family:"Cabin",sans-serif;font-size:13px;font-weight:700;color:var(--ink);text-decoration:underline}

/* who */
.who{height:499px;display:flex}
.who-img{width:600px;height:100%;background:radial-gradient(circle at 38% 62%,#d99a2e 0%,#8a4b16 25%,#2a1a12 55%,#140f12 100%)}
.who-copy{width:600px;background:var(--green);color:var(--white);padding:76px 50px 0 52px}
.who-copy h2{font-size:33px;font-weight:400}
.who-copy h2 b{font-weight:700}
.who-copy .rule{margin:14px 0 0;background:var(--white)}
.who-copy p{margin-top:30px;font-size:14px;line-height:30px}
.who-copy .btn{margin-top:34px;width:146px;height:44px;line-height:44px;font-size:16px}

/* testimonials */
.testimonials{height:611px;background:var(--gray-band)}
.testimonials .section-title{padding-top:84px}
.people{position:absolute;top:182px;left:97px;display:flex;gap:65px}
.person{width:190px;text-align:center}
.avatar{width:190px;height:190px;border-radius:50%;border:3px solid var(--green);padding:7px}
.avatar div{width:100%;height:100%;border-radius:50%;background:linear-gradient(180deg,#d8d8d8,#8c8c8c)}
.person h4{margin-top:22px;font-size:16px;font-weight:700}
.stars{color:var(--star);font-size:13px;letter-spacing:2px;margin-top:2px}
.person p{margin:6px -12px 0;font-style:italic;font-size:14px;line-height:30px;color:var(--muted)}

/* what we do */
.what{height:772px;background:var(--white)}
.what .section-title{padding-top:80px}
.what .lead{position:absolute;top:164px;left:130px;width:940px;text-align:center;font-size:14px;line-height:30px;color:var(--muted)}
.services{position:absolute;top:302px;left:107px;display:flex;gap:29px}
.service{width:310px;text-align:center}
.service-img{height:202px;border-radius:3px}
.service h3{margin-top:20px;font-size:16px;font-weight:700;letter-spacing:.2px}
.service .rule{width:34px;height:3px;margin-top:10px}
.service p{margin-top:10px;font-size:15px;line-height:30px;color:var(--muted);padding:0 20px}
.arrow{position:absolute;top:2955px}

/* cta */
.cta-band{height:331px;background:linear-gradient(180deg,#1ebf6c,#169f5a)}
.cta-band h2{position:absolute;top:88px;width:100%;text-align:center;color:var(--white);font-size:33px;font-weight:700;line-height:52px}
.cta-band .btn{position:absolute;top:215px;left:462px;width:276px;height:45px;line-height:45px;font-size:16px}
.cta-wave{position:absolute;bottom:0;left:0}

/* footer */
.site-footer{height:372px;background:var(--navy);color:var(--white)}
.foot-col{position:absolute;top:74px}
.foot-col h4{font-size:15px;font-weight:700;margin-bottom:12px}
.foot-col li{list-style:none;font-size:14px;line-height:30px}
.foot-brand{left:49px;top:70px}
.foot-brand .brand{font-size:20px}
.foot-brand .brand-dot{width:28px;height:28px}
.foot-brand p{margin-top:18px;font-size:14px;line-height:30px;width:270px}
.socials{display:flex;gap:11px;margin-top:14px}
.socials span{width:32px;height:32px;border-radius:50%;background:var(--white);display:block}
.foot-news p{font-size:14px;line-height:30px;width:270px}
.email{margin-top:16px;width:287px;height:44px;background:var(--white);display:flex;align-items:center;padding:0 12px;color:#888;font-size:12px}
.email svg{margin-left:auto}
.copyright{position:absolute;top:322px;width:100%;text-align:center;font-size:11px}
.copyright b{color:var(--green);font-weight:700}
</style>
</head>
<body>

<header class="hero">
  <div class="hero-art" role="img" aria-label="Dark digital particle wave background"></div>
  <div class="topbar">
    <div class="brand"><span class="brand-dot"></span>LEDGERWISE FORGE</div>
    <nav class="nav">
      <a href="#">HOME</a><a href="#">SERVICES</a><a href="#">LEDGERWISE FORGE METHOD</a><a href="#">TESTIMONIALS</a><a href="#">BLOG</a><a href="#">ABOUT US</a>
    </nav>
    <a class="btn btn-green" href="#">CONTACT US</a>
  </div>
  <h1>YOUR OWN CRYPTOCURRENCY. SECURE, EASY TO USE,<br>AND BUILT BY AN EXPERT TEAM.</h1>
  <a class="btn btn-green cta" href="#">SCHEDULE FREE CONSULTATION</a>
  <svg class="scroll-down" width="40" height="40" viewBox="0 0 40 40"><circle cx="20" cy="20" r="18.5" fill="none" stroke="#fff" stroke-width="2"/><path d="M14 17l6 6 6-6" fill="none" stroke="#fff" stroke-width="2"/></svg>
  <svg class="hero-wave" width="1200" height="80" viewBox="0 0 1200 80" preserveAspectRatio="none">
    <path d="M0 40 C300 20 600 90 1200 10 L1200 80 L0 80Z" fill="#8a8d92"/>
    <path d="M0 58 C300 40 650 110 1200 34 L1200 80 L0 80Z" fill="#f2f2f2"/>
  </svg>
</header>

<section class="intro">
  <p>Ledgerwise Forge adds professionalism to cryptocurrency development. Our done-for-you service covers everything from development and IT operations to ongoing support. You have access to a full team, for less than the typical cost of a single developer.</p>
</section>

<section class="why">
  <h2 class="section-title">Why choose <b>Ledgerwise Forge</b></h2>
  <div class="rule"></div>
  <div class="cards">
    <article class="card">
      <div class="card-img" role="img" aria-label="Coins on a trading data screen" style="background:linear-gradient(135deg,#e8c3b8,#a5562f 60%,#3c2a2a)"></div>
      <h3>VALUE</h3>
      <p>A team of experts, regular updates, and fixed costs</p>
      <a class="more" href="#">LEARN MORE</a>
    </article>
    <article class="card">
      <div class="card-img" role="img" aria-label="Business handshake over a glowing globe" style="background:linear-gradient(135deg,#4d6278,#1d3656 55%,#0e1828)"></div>
      <h3>SUPPORT</h3>
      <p>Receive advice and other services, beyond development.</p>
      <a class="more" href="#">LEARN MORE</a>
    </article>
    <article class="card">
      <div class="card-img" role="img" aria-label="Blockchain network icons" style="background:radial-gradient(circle at 45% 50%,#8a6a3a,#1f4e6c 45%,#0a1e30)"></div>
      <h3>COMMITMENT</h3>
      <p>Enjoy regular updates and new features.</p>
      <a class="more" href="#">LEARN MORE</a>
    </article>
  </div>
</section>

<section class="who">
  <div class="who-img" role="img" aria-label="Gold coins in front of a trading chart"></div>
  <div class="who-copy">
    <h2>Who <b>we are</b></h2>
    <div class="rule"></div>
    <p>Lorem ipsum dolor sit amet, consectetur adipiscing elit, sed do eiusmod tempor incididunt ut labore et dolore magna aliqua. Quis ipsum suspendisse ultrices gravida. Risus commodo viverra maecenas accumsan lacus vel facilisis. Lorem ipsum dolor sit amet, consectetur adipiscing elit, sed do eiusmod tempor incididunt ut labore et dolore magna aliqua.</p>
    <a class="btn btn-white" href="#">LEARN MORE</a>
  </div>
</section>

<section class="testimonials">
  <h2 class="section-title">Our Client <b>Testimonials</b></h2>
  <div class="rule"></div>
  <div class="people">
    <div class="person"><div class="avatar"><div role="img" aria-label="Client portrait"></div></div><h4>JOHN DOE</h4><div class="stars">★★★★★</div><p>Lorem ipsum dolor sit amet, consectetur adipiscing elit, sed do eiusmod tempor</p></div>
    <div class="person"><div class="avatar"><div role="img" aria-label="Client portrait"></div></div><h4>JOHN DOE</h4><div class="stars">★★★★★</div><p>Lorem ipsum dolor sit amet, consectetur adipiscing elit, sed do eiusmod tempor</p></div>
    <div class="person"><div class="avatar"><div role="img" aria-label="Client portrait"></div></div><h4>JOHN DOE</h4><div class="stars">★★★★★</div><p>Lorem ipsum dolor sit amet, consectetur adipiscing elit, sed do eiusmod tempor</p></div>
    <div class="person"><div class="avatar"><div role="img" aria-label="Client portrait"></div></div><h4>JOHN DOE</h4><div class="stars">★★★★★</div><p>Lorem ipsum dolor sit amet, consectetur adipiscing elit, sed do eiusmod tempor</p></div>
  </div>
</section>

<section class="what">
  <h2 class="section-title">What <b>We Do</b></h2>
  <div class="rule"></div>
  <p class="lead">Ledgerwise Forge provides a complete service that handles the development, IT operations and support for your cryptocurrency. Cryptocurrency development can be difficult and complex, and a quality development team is hard to find and expensive. Ledgerwise Forge has an experienced team that has helped several clients launch and enhance their cryptocurrencies, including successfully running the Norvane cryptocurrency since 2017, and writing a next-generation cryptocurrency from scratch.</p>
  <div class="services">
    <article class="service">
      <div class="service-img" role="img" aria-label="Glowing coin on a circuit platform" style="background:radial-gradient(circle at 55% 55%,#3b6cff,#2a2f8a 40%,#141a4a)"></div>
      <h3>LEDGER CREATION &amp; LAUNCH</h3><div class="rule"></div>
      <p>Lorem ipsum dolor sit amet, consectetur adipiscing elit, sed do eiusmod tempor incididunt ut labore.</p>
      <a class="more" href="#">LEARN MORE</a>
    </article>
    <article class="service">
      <div class="service-img" role="img" aria-label="Developer at a bank of monitors" style="background:linear-gradient(160deg,#2e5f86,#153351 55%,#0a1524)"></div>
      <h3>LEDGER DEVELOPMENT</h3><div class="rule"></div>
      <p>Lorem ipsum dolor sit amet, consectetur adipiscing elit, sed do eiusmod tempor incididunt ut labore.</p>
      <a class="more" href="#">LEARN MORE</a>
    </article>
    <article class="service">
      <div class="service-img" role="img" aria-label="Hands using a holographic phone interface" style="background:radial-gradient(circle at 50% 45%,#2f8a8c,#163e48 50%,#0b1a20)"></div>
      <h3>LEDGER OPERATIONS</h3><div class="rule"></div>
      <p>Lorem ipsum dolor sit amet, consectetur adipiscing elit, sed do eiusmod tempor incididunt ut labore.</p>
      <a class="more" href="#">LEARN MORE</a>
    </article>
  </div>
</section>
<svg class="arrow" style="left:52px" width="22" height="40" viewBox="0 0 22 40"><path d="M19 2L3 20l16 18" fill="none" stroke="#333" stroke-width="2.5"/></svg>
<svg class="arrow" style="left:1126px;top:2962px" width="22" height="40" viewBox="0 0 22 40"><path d="M3 2l16 18L3 38" fill="none" stroke="#333" stroke-width="2.5"/></svg>

<section class="cta-band">
  <h2>LOREM IPSUM DOLOR SIT AMET, CONSECTETUR ADIPI<br>SED DO EIUSMOD TEMPOR INCIDIDUNT UT LA.</h2>
  <a class="btn btn-white" href="#">SCHEDULE FREE CONSULTATION</a>
  <svg class="cta-wave" width="1200" height="70" viewBox="0 0 1200 70" preserveAspectRatio="none">
    <path d="M0 30 C350 60 700 0 1200 20 L1200 70 L0 70Z" fill="#0e6b3c"/>
    <path d="M0 48 C380 75 760 12 1200 38 L1200 70 L0 70Z" fill="#0b111c"/>
  </svg>
</section>

<footer class="site-footer">
  <div class="foot-col foot-brand">
    <div class="brand"><span class="brand-dot"></span>LEDGERWISE FORGE</div>
    <p>Lorem ipsum dolor sit amet, consectetur adipiscing elit, sed do eiusmod .</p>
    <div class="socials"><span></span><span></span><span></span><span></span></div>
  </div>
  <div class="foot-col" style="left:392px">
    <h4>WHAT WE DO</h4>
    <ul><li>Ledger Creation &amp; Launch</li><li>Ledger Development</li><li>Ledger Operations</li><li>Ledger Support</li></ul>
  </div>
  <div class="foot-col" style="left:641px">
    <h4>QUICK MENU</h4>
    <ul><li>Home</li><li>Services</li><li>Ledgerwise Forge Method</li><li>Testimonials</li><li>Blog</li><li>About Us</li></ul>
  </div>
  <div class="foot-col foot-news" style="left:863px">
    <h4>NEWSLETTER</h4>
    <p>Lorem ipsum dolor sit amet, consec tetur adipiscing elit sed do.</p>
    <div class="email">Enter The Email
      <svg width="18" height="18" viewBox="0 0 18 18"><path d="M1 8L17 1l-6 16-3-6z" fill="#1fc46f"/></svg>
    </div>
  </div>
  <p class="copyright">© Copyright 2021 <b>Ledgerwise Forge</b>. All Rights Reserved</p>
</footer>

</body>
</html>
```